Poster

I need a poster for my business, www.coastalsupperroutesnerja.example which some information about the most important activities (Sangria Tasting, Iberian Ham, Charcuteries & Sherry Wine Tasting, Sailboat Experiences and Picnic Experiences). A3 Format. Social media included (@coastalsupperroutescsr), contact information included.

```html
<!DOCTYPE html>
<html lang="en">
<head>
<meta charset="utf-8">
<title>Coastal Supper Routes Nerja – Activities</title>
<link rel="stylesheet" href="https://fonts.googleapis.com/css2?family=Cinzel:wght@400&family=Quicksand:wght@600&family=Montserrat:ital,wght@0,500;0,600;1,300&display=swap">
<style>
  :root {
    --paper: #f6f6f6;
    --orange: #f2a51d;
    --ink: #111111;
    --brand-grey: #555555;
    --white: #ffffff;
  }
  * { margin: 0; padding: 0; box-sizing: border-box; }
  html, body { width: 848px; height: 1200px; overflow: hidden; background: var(--paper); }
  .poster { position: relative; width: 848px; height: 1200px; background: var(--paper); overflow: hidden; }
  .poster-art { position: absolute; inset: 0; }
  .brand { position: absolute; left: 42px; top: 56px; display: flex; align-items: center; gap: 14px; }
  .brand-mark { width: 22px; height: 22px; background: var(--orange); }
  .brand-name {
    font-family: "Montserrat", sans-serif; font-weight: 600; font-size: 25px;
    line-height: 1.2; color: var(--brand-grey); text-transform: uppercase; letter-spacing: 0.5px;
  }
  .web-text, .handle-text { fill: var(--white); }
  .web-text { font-family: "Montserrat", sans-serif; font-weight: 500; font-size: 29px; }
  .handle-text { font-family: "Montserrat", sans-serif; font-weight: 300; font-style: italic; font-size: 32px; }
  .title { font-family: "Cinzel", serif; font-weight: 400; font-size: 142px; fill: var(--ink); }
  .activity-list { position: absolute; left: 30px; top: 490px; list-style: none; }
  .activity {
    position: absolute; left: 0; display: flex; align-items: flex-start; gap: 6px;
    font-family: "Quicksand", sans-serif; font-weight: 600; font-size: 31px; line-height: 41px;
    color: var(--ink); white-space: nowrap;
  }
  .activity-star { width: 29px; height: 29px; margin-top: 6px; flex: none; fill: var(--orange); }
</style>
</head>
<body>
<div class="poster">
  <svg class="poster-art" width="848" height="1200" viewBox="0 0 848 1200" xmlns="http://www.w3.org/2000/svg">
    <defs>
      <clipPath id="wave-clip">
        <path d="M848 290 C 810 340 790 380 760 400 C 700 450 640 480 560 510 C 480 540 440 560 434 640 L 434 830 C 430 900 400 940 330 965 C 260 985 160 960 90 965 C 40 970 15 990 0 1010 L 0 1200 L 848 1200 Z"/>
      </clipPath>
      <linearGradient id="sunset" x1="0" y1="0" x2="0" y2="1">
        <stop offset="0" stop-color="#f4a86a"/>
        <stop offset="0.22" stop-color="#d9826e"/>
        <stop offset="0.4" stop-color="#6c4d6e"/>
        <stop offset="1" stop-color="#2d2540"/>
      </linearGradient>
      <linearGradient id="chef" x1="0" y1="0" x2="1" y2="1">
        <stop offset="0" stop-color="#c7b49b"/><stop offset="0.5" stop-color="#6fb4c4"/><stop offset="1" stop-color="#5a4a3c"/>
      </linearGradient>
      <linearGradient id="friends" x1="0" y1="0" x2="1" y2="1">
        <stop offset="0" stop-color="#d9b8a0"/><stop offset="0.6" stop-color="#e8e6e2"/><stop offset="1" stop-color="#7a2a2e"/>
      </linearGradient>
      <linearGradient id="basket" x1="0" y1="0" x2="1" y2="1">
        <stop offset="0" stop-color="#8fa2b8"/><stop offset="0.5" stop-color="#dfe4ec"/><stop offset="1" stop-color="#9a6a44"/>
      </linearGradient>
      <linearGradient id="beach" x1="0" y1="0" x2="1" y2="1">
        <stop offset="0" stop-color="#d6cfc6"/><stop offset="0.5" stop-color="#b9b3ad"/><stop offset="1" stop-color="#8d8680"/>
      </linearGradient>
      <linearGradient id="sangria" x1="0" y1="0" x2="0" y2="1">
        <stop offset="0" stop-color="#efefef"/><stop offset="0.55" stop-color="#5a1e26"/><stop offset="1" stop-color="#5b3c8c"/>
      </linearGradient>
      <linearGradient id="olives" x1="0" y1="0" x2="1" y2="1">
        <stop offset="0" stop-color="#2a2420"/><stop offset="0.6" stop-color="#1a1715"/><stop offset="1" stop-color="#3d6e4f"/>
      </linearGradient>
    </defs>

    <g clip-path="url(#wave-clip)">
      <g role="img" aria-label="Photo of the sea at sunset">
        <rect x="0" y="280" width="848" height="920" fill="url(#sunset)"/>
      </g>
      <rect x="0" y="970" width="848" height="230" fill="#2b2320"/>
      <g role="img" aria-label="Photo of a host cooking paella in a wine shop">
        <rect x="428" y="548" width="316" height="252" fill="url(#chef)"/>
      </g>
      <g role="img" aria-label="Photo of a picnic basket with cheese and croissants by the water">
        <rect x="664" y="747" width="184" height="224" fill="url(#basket)"/>
      </g>
      <g role="img" aria-label="Photo of friends sharing sangria">
        <rect x="434" y="788" width="230" height="201" fill="url(#friends)"/>
      </g>
      <g role="img" aria-label="Photo of a picnic spread on the beach">
        <rect x="0" y="940" width="324" height="260" fill="url(#beach)"/>
      </g>
      <g role="img" aria-label="Photo of sangria glasses with cheese">
        <rect x="324" y="1037" width="219" height="163" fill="url(#sangria)"/>
      </g>
      <g role="img" aria-label="Photo of olives and cured meat on a board">
        <rect x="543" y="1037" width="305" height="163" fill="url(#olives)"/>
      </g>
    </g>

    <polygon points="114,201 789,201 765,251 90,251" fill="var(--orange)"/>
    <text class="web-text" x="126" y="241" textLength="630" lengthAdjust="spacingAndGlyphs">www.coastalsupperroutesnerja.example</text>

    <text class="title" x="64" y="393" textLength="712" lengthAdjust="spacingAndGlyphs">ACTIVITIES</text>

    <polygon points="361,989 819,989 797,1037 340,1037" fill="var(--orange)"/>
    <text class="handle-text" x="388" y="1025" textLength="381" lengthAdjust="spacingAndGlyphs">@coastalsupperroutescsr</text>
  </svg>

  <div class="brand">
    <span class="brand-mark"></span>
    <p class="brand-name">Coastal Supper<br>Routes Nerja</p>
  </div>

  <ul class="activity-list">
    <li class="activity" style="top:0px"><svg class="activity-star" viewBox="0 0 20 20"><path d="M10 0 C11 7 13 9 20 10 C13 11 11 13 10 20 C9 13 7 11 0 10 C7 9 9 7 10 0Z"/></svg>Sangria Tasting</li>
    <li class="activity" style="top:79px"><svg class="activity-star" viewBox="0 0 20 20"><path d="M10 0 C11 7 13 9 20 10 C13 11 11 13 10 20 C9 13 7 11 0 10 C7 9 9 7 10 0Z"/></svg>Iberian Ham</li>
    <li class="activity" style="top:158px"><svg class="activity-star" viewBox="0 0 20 20"><path d="M10 0 C11 7 13 9 20 10 C13 11 11 13 10 20 C9 13 7 11 0 10 C7 9 9 7 10 0Z"/></svg><span>Charcuteries &amp;<br>Sherry Wine Tasting</span></li>
    <li class="activity" style="top:279px"><svg class="activity-star" viewBox="0 0 20 20"><path d="M10 0 C11 7 13 9 20 10 C13 11 11 13 10 20 C9 13 7 11 0 10 C7 9 9 7 10 0Z"/></svg>Sailboat Experiences</li>
    <li class="activity" style="top:358px"><svg class="activity-star" viewBox="0 0 20 20"><path d="M10 0 C11 7 13 9 20 10 C13 11 11 13 10 20 C9 13 7 11 0 10 C7 9 9 7 10 0Z"/></svg>Picnic Experiences</li>
  </ul>
</div>
</body>
</html>
```